Local Flower Farm Needs Business Card Design

I need business cards designed for a flower farm based in Eudora, Kansas.
Business Info:
We are a local cut flower farm located in Eudora, Kansas, founded by Corinne Haldwick. What started as a passion for agriculture and search for more joy in daily life has blossomed into a small business dedicated to providing the community with beautiful, fresh, and sustainable flowers. We specialize in local, seasonal blooms, ensuring that every petal reflects the care and dedication we pour into our craft. Our mission is to deliver the highest quality flowers directly to our customers through local farmers markets and to florists who share our commitment to sustainability. Join us in celebrating the beauty of nature, one bloom at a time!
Contact Details:
Corinne Haldwick
Owner
Phone 913-555-0147
Facebook: Rosalind Thorpe Gardens
Instagram: @RosalindThorpeGardens
Website: RosalindThorpeGardens.example
Target Market(s)
Wholesale to Florists and Direct to Consumer via Farmers Market
Industry/Entity Type
Florist, Farm
Contact Information for Business Card
Name, Contact Info, Logo
Look and feel
Each slider illustrates characteristics of the customer's brand and the style your logo design should communicate.

```html
<!DOCTYPE html>
<html lang="en">
<head>
<meta charset="utf-8">
<title>Rosalind Thorpe Gardens – Business Card</title>
<link href="https://fonts.googleapis.com/css2?family=Montserrat:wght@400;500;700&display=swap" rel="stylesheet">
<style>
  :root {
    --forest: #0e2a2c;
    --paper: #ffffff;
    --ink: #0e2a2c;
    --muted: #3a4a4b;
    --backdrop: #e9ecec;
  }
  * { box-sizing: border-box; margin: 0; padding: 0; }
  html, body { width: 1200px; height: 900px; overflow: hidden; }
  body {
    background: var(--backdrop);
    font-family: "Montserrat", Arial, sans-serif;
    position: relative;
  }
  .card {
    position: absolute;
    left: 250px;
    width: 700px;
    height: 400px;
    border-radius: 30px;
    overflow: hidden;
  }
  .card--back { top: 30px; background: var(--forest); }
  .card--front { top: 470px; background: var(--paper); }

  .brand-seal {
    position: absolute;
    border-radius: 50%;
    display: flex;
    align-items: center;
    justify-content: center;
    text-align: center;
    font-weight: 500;
    letter-spacing: 0.12em;
    text-transform: uppercase;
    z-index: 1;
  }
  .card--back .brand-seal {
    width: 270px; height: 270px;
    left: 215px; top: 65px;
    border: 1.5px solid var(--paper);
    color: var(--paper);
    font-size: 22px;
    line-height: 1.5;
  }
  .card--front .brand-seal {
    width: 220px; height: 220px;
    left: 450px; top: 28px;
    border: 1.5px solid var(--ink);
    color: var(--ink);
    font-size: 18px;
    line-height: 1.5;
  }

  .holder { position: absolute; left: 50px; top: 105px; z-index: 1; }
  .holder__name { font-size: 26px; font-weight: 700; color: var(--ink); }
  .holder__role { font-size: 14px; color: var(--muted); margin-top: 6px; }

  .contact-list {
    position: absolute;
    left: 50px; top: 218px;
    list-style: none;
    font-size: 15px;
    color: var(--ink);
    z-index: 1;
  }
  .contact-list li { display: flex; align-items: center; gap: 9px; height: 24px; white-space: nowrap; }
  .contact-list svg { width: 14px; height: 14px; flex: none; }

  .wave { position: absolute; left: 0; top: 0; width: 700px; height: 400px; }
</style>
</head>
<body>

  <section class="card card--back" aria-label="Card back">
    <div class="brand-seal">Rosalind<br>Thorpe<br>Gardens</div>
  </section>

  <section class="card card--front" aria-label="Card front">
    <svg class="wave" viewBox="0 0 700 400" aria-hidden="true">
      <path d="M0,350 C250,360 450,300 700,255 L700,400 L0,400 Z" fill="var(--forest)"/>
      <path d="M0,372 C260,380 480,322 700,274" fill="none" stroke="var(--paper)" stroke-width="2.5"/>
    </svg>

    <div class="holder">
      <h1 class="holder__name">Corinne Haldwick</h1>
      <p class="holder__role">Owner</p>
    </div>

    <div class="brand-seal">Rosalind<br>Thorpe<br>Gardens</div>

    <ul class="contact-list">
      <li>
        <svg viewBox="0 0 24 24" aria-hidden="true"><path d="M6.6 10.8a15 15 0 0 0 6.6 6.6l2.2-2.2a1 1 0 0 1 1-.25 11.4 11.4 0 0 0 3.6.57 1 1 0 0 1 1 1V20a1 1 0 0 1-1 1A17 17 0 0 1 3 4a1 1 0 0 1 1-1h3.5a1 1 0 0 1 1 1c0 1.25.2 2.45.57 3.57a1 1 0 0 1-.25 1z" fill="var(--ink)"/></svg>
        913-555-0147
      </li>
      <li>
        <svg viewBox="0 0 24 24" aria-hidden="true"><circle cx="12" cy="12" r="10" fill="var(--ink)"/></svg>
        Rosalind Thorpe Gardens
      </li>
      <li>
        <svg viewBox="0 0 24 24" aria-hidden="true"><circle cx="12" cy="12" r="10" fill="var(--ink)"/></svg>
        @RosalindThorpeGardens
      </li>
      <li>
        <svg viewBox="0 0 24 24" aria-hidden="true"><circle cx="12" cy="12" r="9.5" fill="none" stroke="var(--ink)" stroke-width="2"/><path d="M2.5 12h19M12 2.5c3 3 3 16 0 19M12 2.5c-3 3-3 16 0 19" fill="none" stroke="var(--ink)" stroke-width="1.6"/></svg>
        www.RosalindThorpeGardens.example
      </li>
    </ul>
  </section>

</body>
</html>
```